I want to redesign the Tallvex corporate website

Morrowdale Farms Limited (Tallvex) is a Nigerian integrated agribusiness and premium food company operating across agriculture, food processing and nationwide FMCG distribution.
We are redesigning our corporate website to reflect our evolution into a modern, premium food company capable of serving institutional buyers, distributors, retailers, investors and consumers. The new website should feel comparable to the websites of leading global food brands — not a typical agricultural website.

Target Market(s)

Nigeria / Africa

Industry/Entity Type

FMCG

Coding

Coded - Design and coding required

Number of Pages Required

5+ page

Colors

Designer to choose colors to be used in the design.

Requirements
Must have
• The website must communicate the following attributes consistently across every page, in both design and language. Premium Quality of finish signals quality of product , Clean Uncluttered layouts, disciplined use of elements ,Modern Current design language, not dated conventions ,Innovative and Forward-looking, technology-enabled , Sustainable Responsible practice made visible Nigerian with global standards, Proudly local in origin, international in execution
Nice to have
• Lots of white space , Fast loading, Premium photography,Mobile-first,Elegant typography,Minimal clutter, Rounded elements,High-end corporate feel, Smooth curved section transitions, Soft shadows
Should not have
• The new website should feel comparable to the websites of leading global food brands — not a typical agricultural website. Also do not copy the business profile as website , its is just a guide !

```html
<!DOCTYPE html>
<html lang="en">
<head>
<meta charset="utf-8">
<title>Tallvex — Integrated Agriculture. Nourishing Lives.</title>
<link href="https://fonts.googleapis.com/css2?family=Figtree:wght@400;500;600&family=Newsreader:opsz,wght@6..72,400;6..72,500&display=swap" rel="stylesheet">
<style>
:root{
  --forest:#132f1c;
  --forest-2:#1a3d24;
  --brand:#1d4a2a;
  --leaf:#6aa84f;
  --leaf-soft:#e9f3e2;
  --cream:#f7f4ec;
  --ink:#1b1f1c;
  --muted:#5d635f;
  --line:#e6e2d8;
  --orange:#f26a1b;
  --white:#ffffff;
  --serif:"Newsreader",Georgia,serif;
  --sans:"Figtree",Helvetica,Arial,sans-serif;
}
*{box-sizing:border-box;margin:0;padding:0}
html,body{width:1200px;height:4580px;overflow:hidden}
body{font-family:var(--sans);color:var(--ink);background:var(--white);position:relative}
.abs{position:absolute}
.serif{font-family:var(--serif);font-weight:400;letter-spacing:-0.02em}

/* nav */
.nav{position:absolute;top:0;left:0;width:1200px;height:64px;background:var(--white);z-index:5}
.brand{position:absolute;left:124px;top:18px;display:flex;align-items:center;gap:8px;font-family:var(--sans);font-weight:500;font-size:25px;color:var(--brand)}
.brand-dot{width:12px;height:12px;border-radius:50%;background:var(--leaf)}
.nav-links{position:absolute;left:280px;top:20px;display:flex;gap:6px;font-size:12.5px;color:#444}
.nav-links span{padding:5px 12px;border-radius:20px}
.nav-links .active{background:var(--leaf-soft);color:var(--brand)}
.nav-cta{position:absolute;right:124px;top:13px;height:38px;padding:0 20px;border-radius:20px;background:var(--brand);color:#fff;font-size:12.5px;font-weight:500;display:flex;align-items:center}

/* pills */
.pill{display:inline-flex;align-items:center;gap:7px;height:24px;padding:0 12px;border-radius:14px;font-size:10px;letter-spacing:.16em;font-weight:500;text-transform:uppercase;border:1px solid #cfe4c3;background:var(--leaf-soft);color:var(--brand)}
.pill::before{content:"";width:5px;height:5px;border-radius:50%;background:var(--leaf)}
.pill.dark{background:rgba(255,255,255,.04);border-color:rgba(255,255,255,.25);color:#e8efe6}

.btn{display:inline-flex;align-items:center;justify-content:center;height:46px;padding:0 28px;border-radius:24px;font-size:13.5px;font-weight:500}
.btn-green{background:var(--brand);color:#fff}
.btn-white{background:#fff;color:var(--brand)}

/* hero */
.hero{position:absolute;top:64px;left:0;width:1200px;height:680px;overflow:hidden}
.hero-bg{position:absolute;inset:0;background:radial-gradient(ellipse at 30% 30%,#2b4f2a 0%,#1b3a1f 45%,#0f2715 100%)}
.hero h1{position:absolute;left:124px;top:136px;font-size:61px;line-height:64px;color:#fff}
.hero .lead{position:absolute;left:124px;top:288px;width:490px;font-size:14.5px;line-height:24px;color:#dfe7dc}
.hero .actions{position:absolute;left:124px;top:393px;display:flex;gap:14px}
.hero .actions .btn-green{background:#245a33}
.hero-rule{position:absolute;left:124px;top:505px;width:952px;height:1px;background:rgba(255,255,255,.18)}
.stat{position:absolute;top:536px;color:#fff}
.stat b{display:block;font-family:var(--serif);font-weight:400;font-size:39px;line-height:44px}
.stat small{display:block;margin-top:8px;font-size:10.5px;letter-spacing:.16em;color:#c8d3c5}
.hero-wave{position:absolute;left:0;bottom:0;width:1200px;height:130px}

/* who */
.who{position:absolute;top:744px;left:0;width:1200px;height:640px;background:var(--cream)}
.h2{font-family:var(--serif);font-weight:400;font-size:41px;line-height:45px;letter-spacing:-0.02em;color:var(--ink)}
.body{font-size:14.5px;line-height:24px;color:#3b403c}
.who-photo{position:absolute;left:628px;top:101px;width:446px;height:420px;border-radius:26px;background:linear-gradient(160deg,#f4efe8,#ead9c8 55%,#c96b3a 100%);box-shadow:0 20px 50px rgba(0,0,0,.08)}
.badge{position:absolute;left:601px;top:442px;width:185px;height:105px;border-radius:16px;background:#fff;box-shadow:0 16px 40px rgba(0,0,0,.08);padding:20px 19px}
.badge b{font-family:var(--serif);font-weight:400;font-size:25px;display:block;line-height:28px}
.badge span{font-size:11px;line-height:16px;color:#444;display:block;margin-top:6px}
.who-wave{position:absolute;left:0;bottom:0;width:1200px;height:100px}

/* products */
.products{position:absolute;top:1340px;left:0;width:1200px;height:810px;background:#fff}
.btn-outline{position:absolute;right:124px;top:153px;height:36px;padding:0 21px;border:1px solid #d8d8d3;border-radius:20px;font-size:12px;display:flex;align-items:center;color:var(--ink)}
.card{position:absolute;top:244px;width:313px;height:470px;border-radius:14px;background:#fff;box-shadow:0 10px 30px rgba(0,0,0,.08);overflow:hidden}
.card-media{height:240px}
.card h3{position:absolute;left:27px;top:270px;font-family:var(--serif);font-weight:400;font-size:22px}
.card .tag{position:absolute;left:27px;top:302px;font-size:11.5px;color:#4a8a34}
.card p{position:absolute;left:27px;top:334px;width:260px;font-size:11.5px;line-height:19px;color:#555}
.card .more{position:absolute;left:27px;top:427px;font-size:11.5px;color:var(--brand);font-weight:500;display:flex;gap:8px;align-items:center}

/* business */
.business{position:absolute;top:2150px;left:0;width:1200px;height:967px;background:radial-gradient(ellipse at 20% 20%,#1f4227 0%,#133019 60%,#0f2816 100%)}
.business .h2,.cta .h2{color:#fff}
.tile{position:absolute;width:303px;height:211px;border-radius:14px;overflow:hidden}
.tile::after{content:"";position:absolute;inset:0;background:linear-gradient(180deg,rgba(0,0,0,0) 45%,rgba(10,30,15,.75) 100%)}
.tile span{position:absolute;left:20px;bottom:20px;z-index:2;font-family:var(--serif);font-size:17.5px;color:#fff}

/* sustainability */
.sust{position:absolute;top:3117px;left:0;width:1200px;height:567px;background:var(--cream)}
.sust-photo{position:absolute;left:124px;top:110px;width:449px;height:347px;border-radius:26px;background:linear-gradient(150deg,#e9e4dc,#cdb29a 45%,#7a4a2c 75%,#d9b43d 100%);box-shadow:0 20px 50px rgba(0,0,0,.1)}
.sstat{position:absolute;top:345px}
.sstat b{display:block;font-family:var(--serif);font-weight:400;font-size:41px;line-height:44px;color:var(--brand)}
.sstat small{display:block;margin-top:6px;font-size:10.5px;letter-spacing:.16em;color:#777}

/* cta */
.cta{position:absolute;top:3684px;left:0;width:1200px;height:455px;background:var(--forest);text-align:center}
.btn-orange{background:var(--orange);color:#fff}

/* footer */
.footer{position:absolute;top:4139px;left:0;width:1200px;height:441px;background:#fff}
.col{position:absolute;top:73px}
.col h4{font-size:12.5px;letter-spacing:.16em;font-weight:600;margin-bottom:17px}
.col a{display:block;font-size:11.5px;color:#333;line-height:26.6px;text-decoration:none}
.foot-rule{position:absolute;left:124px;top:377px;width:952px;height:1px;background:var(--line)}
.foot-bottom{position:absolute;top:396px;font-size:10.5px;color:#666}
</style>
</head>
<body>

<header class="nav">
  <div class="brand"><span class="brand-dot"></span>Morrowdale</div>
  <nav class="nav-links">
    <span class="active">Home</span><span>About Us</span><span>Products</span><span>Our Business</span><span>Sustainability</span><span>Investors</span><span>News &amp; Media</span><span>More</span>
  </nav>
  <a class="nav-cta">Get in touch</a>
</header>

<section class="hero">
  <div class="hero-bg" role="img" aria-label="Close-up of lush green crop field"></div>
  <div class="abs" style="left:124px;top:82px"><span class="pill dark">Integrated Agriculture · Food Processing · FMCG Distribution</span></div>
  <h1 class="serif">Integrated Agriculture.<br>Nourishing Lives.</h1>
  <p class="lead">Tallvex is a Nigerian agribusiness and premium food company — growing, processing and distributing quality food nationwide, built to a global standard from farm to family table.</p>
  <div class="actions"><a class="btn btn-green">Explore Products</a><a class="btn btn-white">About Tallvex</a></div>
  <div class="hero-rule"></div>
  <div class="stat" style="left:124px"><b>10+</b><small>YEARS OF GROWTH</small></div>
  <div class="stat" style="left:370px"><b>20+</b><small>STATES REACHED</small></div>
  <div class="stat" style="left:613px"><b>5,000+</b><small>FARMERS EMPOWERED</small></div>
  <div class="stat" style="left:857px"><b>3</b><small>PRODUCT LINES</small></div>
  <svg class="hero-wave" viewBox="0 0 1200 130" preserveAspectRatio="none"><path d="M0 128 C250 150 420 60 700 80 C950 98 1080 40 1200 0 L1200 130 L0 130 Z" fill="#f7f4ec"/></svg>
</section>

<section class="who">
  <div class="abs" style="left:124px;top:188px"><span class="pill">Who we are</span></div>
  <h2 class="h2 abs" style="left:124px;top:228px;width:480px">Proudly Nigerian. Built to a global standard.</h2>
  <p class="body abs" style="left:124px;top:334px;width:440px">From modern poultry houses to state-of-the-art processing lines, Tallvex brings together agriculture, manufacturing and distribution under one integrated operation — engineered for quality, consistency and scale.</p>
  <div class="who-photo" role="img" aria-label="Smiling woman enjoying a handful of plantain chips"></div>
  <div class="badge"><b>100%</b><span>Traceable, farm-to-table quality assurance</span></div>
  <svg class="who-wave" viewBox="0 0 1200 100" preserveAspectRatio="none"><path d="M0 30 C300 70 500 70 700 60 C900 50 1080 20 1200 0 L1200 100 L0 100 Z" fill="#ffffff"/></svg>
</section>

<section class="products">
  <div class="abs" style="left:124px;top:40px"><span class="pill">Our Products</span></div>
  <h2 class="h2 abs" style="left:124px;top:84px">Premium food, made naturally.</h2>
  <p class="body abs" style="left:124px;top:142px;width:540px">Three trusted product lines, crafted with quality ingredients and rigorous standards — with more innovation on the way.</p>
  <a class="btn-outline">View all products</a>

  <article class="card" style="left:124px">
    <div class="card-media" role="img" aria-label="Tray of thirty large brown eggs" style="background:linear-gradient(160deg,#c9d2dc,#a97456 55%,#8d5a3d)"></div>
    <h3>Premium Eggs</h3><div class="tag">Good eggs. Better life.</div>
    <p>Grade AA large brown eggs from modern, automated poultry houses with strict biosecurity and full farm-to-table traceability. No antibiotics, no GMOs, no hormones.</p>
    <div class="more">Discover more <svg width="10" height="10" viewBox="0 0 10 10"><path d="M1 5h7M5 2l3 3-3 3" stroke="currentColor" fill="none" stroke-width="1.3"/></svg></div>
  </article>
  <article class="card" style="left:443px">
    <div class="card-media" role="img" aria-label="Pack of plantain chips" style="background:linear-gradient(160deg,#b9c2cc,#9ea8b1 50%,#c6b53c)"></div>
    <h3>Plantain Chips</h3><div class="tag">Real plantain. Real taste.</div>
    <p>Crispy, golden plantain chips made from 100% natural plantain, with just the right amount of salt. Gluten-free, and free from artificial preservatives.</p>
    <div class="more">Discover more <svg width="10" height="10" viewBox="0 0 10 10"><path d="M1 5h7M5 2l3 3-3 3" stroke="currentColor" fill="none" stroke-width="1.3"/></svg></div>
  </article>
  <article class="card" style="left:761px">
    <div class="card-media" role="img" aria-label="Honey jar beside a gift pack of plantain chips" style="background:linear-gradient(160deg,#d9c8b4,#c8893a 45%,#b7302a 85%)"></div>
    <h3>Pure Honey</h3><div class="tag">Sourced from nature. Packed with goodness.</div>
    <p>100% pure, raw honey harvested responsibly and bottled with care. Rich in antioxidants, with a naturally sweet, delicious aroma and zero additives.</p>
    <div class="more">Discover more <svg width="10" height="10" viewBox="0 0 10 10"><path d="M1 5h7M5 2l3 3-3 3" stroke="currentColor" fill="none" stroke-width="1.3"/></svg></div>
  </article>
</section>

<section class="business">
  <div class="abs" style="left:124px;top:94px"><span class="pill dark">Our Business</span></div>
  <h2 class="h2 abs" style="left:124px;top:134px;width:560px">One integrated value chain, end to end.</h2>
  <p class="body abs" style="left:124px;top:238px;width:520px;color:#a9b8a7">From soil to shelf, Tallvex controls quality at every stage — agriculture, processing, quality assurance and nationwide distribution.</p>

  <div class="tile" style="left:124px;top:341px;background:linear-gradient(170deg,#c9ccd0,#9a6a4b 55%,#5a3a28)" role="img" aria-label="Eggs moving along a poultry conveyor"><span>Poultry</span></div>
  <div class="tile" style="left:448px;top:341px;background:linear-gradient(180deg,#c6cdd1,#5b7a4a 40%,#2f5228)" role="img" aria-label="Rows of plantain crops in a farm"><span>Plantain Farming</span></div>
  <div class="tile" style="left:772px;top:341px;background:linear-gradient(180deg,#b9a98f,#9b8a4a 45%,#5c5425)" role="img" aria-label="Food processing factory line"><span>Food Processing</span></div>
  <div class="tile" style="left:124px;top:574px;background:linear-gradient(180deg,#c8ccd0,#7a7f82 50%,#3f4548)" role="img" aria-label="Large distribution warehouse"><span>Distribution</span></div>
  <div class="tile" style="left:448px;top:574px;background:linear-gradient(180deg,#dcdcdc,#b8a089 55%,#6b4c35)" role="img" aria-label="Chef inspecting a tray of eggs"><span>Quality Assurance</span></div>
  <div class="tile" style="left:772px;top:574px;background:linear-gradient(180deg,#c9d3d6,#4f6468 50%,#22302f)" role="img" aria-label="Team meeting in a glass office"><span>Research &amp; Innovation</span></div>

  <div class="abs" style="left:507px;top:828px"><a class="btn btn-white" style="width:186px;padding:0">Explore Our Business</a></div>
</section>

<section class="sust">
  <div class="sust-photo" role="img" aria-label="Friends sharing snacks around a table"></div>
  <div class="abs" style="left:628px;top:96px"><span class="pill">Sustainability</span></div>
  <h2 class="h2 abs" style="left:628px;top:136px;width:440px">Responsible practice, made visible.</h2>
  <p class="body abs" style="left:628px;top:242px;width:440px">We believe premium food and responsible farming go hand in hand. From soil health to farmer welfare, sustainability shapes every decision we make.</p>
  <div class="sstat" style="left:628px"><b>5,000+</b><small>FARMERS SUPPORTED</small></div>
  <div class="sstat" style="left:861px"><b>40%</b><small>WATER USE REDUCED</small></div>
  <div class="abs" style="left:628px;top:435px"><a class="btn btn-green" style="height:36px;padding:0 20px;font-size:12px">Our Sustainability Story</a></div>
</section>

<section class="cta">
  <div style="margin-top:94px"><span class="pill dark">Partner with Tallvex</span></div>
  <h2 class="h2" style="margin:22px auto 0;width:520px">Let's grow something good, together.</h2>
  <p class="body" style="margin:24px auto 0;width:560px;color:#a9b8a7">Whether you're a distributor, retailer, investor or future team member — we'd love to hear from you.</p>
  <div style="margin-top:37px;display:flex;gap:16px;justify-content:center"><a class="btn btn-orange">Get in Touch</a><a class="btn btn-white">For Investors</a></div>
</section>

<footer class="footer">
  <div class="brand" style="top:76px"><span class="brand-dot"></span>Morrowdale</div>
  <p class="abs" style="left:124px;top:127px;width:260px;font-size:12.5px;line-height:19px;color:#333">An integrated Nigerian agribusiness and premium food company — growing nature, nourishing lives, and building global standards from local roots.</p>
  <div class="col" style="left:418px"><h4>EXPLORE</h4><a>Home</a><a>About Us</a><a>Products</a><a>Our Business</a><a>Sustainability</a><a>Investors</a><a>News &amp; Media</a><a>Careers</a><a>Contact</a></div>
  <div class="col" style="left:638px"><h4>PRODUCTS</h4><a>Premium Eggs</a><a>Plantain Chips</a><a>Pure Honey</a><a>Future Products</a></div>
  <div class="col" style="left:859px;width:220px"><h4>CONTACT</h4><a style="line-height:17px;margin:4px 0 6px">12b Adeyemo Close, GRA, Ikeja, Lagos, Nigeria</a><a>+234 800 555 0142</a><a>info@tallvex.food</a><a>tallvex.food</a></div>
  <div class="foot-rule"></div>
  <div class="foot-bottom" style="left:124px">© 2026 Morrowdale Farms Limited. All rights reserved.</div>
  <div class="foot-bottom" style="right:124px">Natural. Sustainable. Responsible. Quality.</div>
</footer>

</body>
</html>
```